Brightbay Orthodontics business card design

Need a business card design that reflects our re-branding (orthodontic office - braces) and a new partnership with a pediatric dental office. We would like to include "for adults and children" on the card as well so adults know they are welcome to get their braces here as well. Office design is modern and would like business card to reflect a modern type look. Here's the text we would like to be included on the card:

Darren Wolcott, DDS, MSD
5214 West Linden Avenue, Suite 204
Cedarmont, NV 76991
555-418-2637
www.brightbayortho.example
info@brightbayortho.example

Can we add the following to the existing designs? Darren Wolcott, DDS, MSD 5214 West Linden Avenue, Suite 204 Cedarmont, NV 76991 555-418-2637

Does anyone have any more vertical designs available? Thanks!

Dental

```html
<!DOCTYPE html>
<html lang="en">
<head>
<meta charset="utf-8">
<title>Brightbay Orthodontics – Business Card</title>
<link rel="stylesheet" href="https://fonts.googleapis.com/css2?family=Montserrat:wght@700&family=Lato:wght@400;700&family=Architects+Daughter&display=swap">
<style>
  :root {
    --bg: #e9e9e9;
    --card: #fbfbfb;
    --edge: #1e1e1e;
    --ink: #1a1a1a;
    --muted: #333333;
    --yellow: #f2e500;
    --blue: #1b74bb;
    --magenta: #e0168a;
    --green: #7cc242;
    --orange: #f39a1e;
    --icon: #2a86c9;
    --mark: #dcdcdc;
  }
  * { box-sizing: border-box; margin: 0; padding: 0; }
  html, body {
    width: 1200px; height: 1116px; overflow: hidden;
    background: var(--bg);
  }
  .canvas {
    width: 1200px; height: 1116px;
    display: flex; align-items: center; justify-content: center;
  }
  .card {
    position: relative;
    width: 600px; height: 1050px;
    background: var(--card);
    border: 4px solid var(--edge);
    display: flex; flex-direction: column;
    box-shadow: 0 10px 30px rgba(0,0,0,0.18);
  }
  .color-bar {
    display: flex; flex: none;
    background: var(--edge); gap: 4px;
    height: 34px;
  }
  .color-bar.top { border-bottom: 4px solid var(--edge); }
  .color-bar.bottom { border-top: 4px solid var(--edge); }
  .color-bar span { flex: 1; }
  .c-yellow { background: var(--yellow); }
  .c-blue { background: var(--blue); }
  .c-magenta { background: var(--magenta); }
  .c-green { background: var(--green); }
  .c-orange { background: var(--orange); }

  .card-body { flex: 1; display: flex; flex-direction: column; align-items: center; }

  .doctor-name {
    margin-top: 36px;
    font: 700 34px/1 "Montserrat", sans-serif;
    color: var(--ink);
  }
  .credentials {
    margin-top: 10px;
    font: 700 18px/1 "Lato", sans-serif;
    color: var(--muted);
    letter-spacing: 0.5px;
  }

  .brand {
    margin-top: 70px;
    display: flex; align-items: center; gap: 22px;
  }
  .brand-mark {
    width: 96px; height: 96px; border-radius: 50%;
    background: var(--mark); flex: none;
  }
  .brand-name {
    font: 700 46px/1.1 "Montserrat", sans-serif;
    color: var(--ink);
  }

  .contact-list {
    list-style: none;
    margin-top: 120px;
    align-self: flex-start;
    margin-left: 56px;
    display: flex; flex-direction: column; gap: 26px;
  }
  .contact-item {
    display: flex; align-items: flex-start; gap: 18px;
    font: 700 25px/1.35 "Lato", sans-serif;
    color: var(--ink);
  }
  .contact-icon { width: 40px; height: 40px; flex: none; margin-top: -2px; }

  .tagline {
    margin-top: auto; margin-bottom: 60px;
    font: 400 30px/1 "Architects Daughter", cursive;
    letter-spacing: 3px;
    color: var(--muted);
  }
</style>
</head>
<body>
<main class="canvas">
  <article class="card">
    <div class="color-bar top">
      <span class="c-yellow"></span><span class="c-blue"></span><span class="c-magenta"></span><span class="c-green"></span><span class="c-orange"></span>
    </div>

    <div class="card-body">
      <h1 class="doctor-name">Darren Wolcott</h1>
      <p class="credentials">DDS, MSD</p>

      <div class="brand">
        <div class="brand-mark"></div>
        <p class="brand-name">Brightbay<br>Orthodontics</p>
      </div>

      <ul class="contact-list">
        <li class="contact-item">
          <svg class="contact-icon" viewBox="0 0 40 40" aria-hidden="true">
            <circle cx="20" cy="20" r="20" fill="var(--icon)"/>
            <path d="M12 16c0-3 3-5 8-5s8 2 8 5l-3 1-1-2h-8l-1 2zM14 19h12l2 9H12z" fill="#fff"/>
            <circle cx="20" cy="23" r="2.5" fill="var(--icon)"/>
          </svg>
          <span>555-418-2637</span>
        </li>
        <li class="contact-item">
          <svg class="contact-icon" viewBox="0 0 40 40" aria-hidden="true">
            <circle cx="20" cy="20" r="20" fill="var(--icon)"/>
            <g fill="none" stroke="#fff" stroke-width="3" stroke-linecap="round">
              <path d="M18 22l-3 3a3.5 3.5 0 0 1-5-5l4-4a3.5 3.5 0 0 1 5 0"/>
              <path d="M22 18l3-3a3.5 3.5 0 0 1 5 5l-4 4a3.5 3.5 0 0 1-5 0"/>
            </g>
          </svg>
          <span>www.brightbayortho.example</span>
        </li>
        <li class="contact-item">
          <svg class="contact-icon" viewBox="0 0 40 40" aria-hidden="true">
            <circle cx="20" cy="20" r="20" fill="var(--icon)"/>
            <rect x="10" y="13" width="20" height="14" rx="1.5" fill="#fff"/>
            <path d="M10.5 13.5L20 21l9.5-7.5" fill="none" stroke="var(--icon)" stroke-width="2"/>
          </svg>
          <span>info@brightbayortho.example</span>
        </li>
        <li class="contact-item">
          <svg class="contact-icon" viewBox="0 0 40 40" aria-hidden="true">
            <circle cx="20" cy="20" r="20" fill="var(--icon)"/>
            <path d="M20 9a7 7 0 0 1 7 7c0 5-7 14-7 14s-7-9-7-14a7 7 0 0 1 7-7z" fill="#fff"/>
            <circle cx="20" cy="16" r="2.8" fill="var(--icon)"/>
          </svg>
          <span>5214 West Linden Avenue, Suite 204<br>Cedarmont, NV 76991</span>
        </li>
      </ul>

      <p class="tagline">FOR ADULTS &amp; CHILDREN</p>
    </div>

    <div class="color-bar bottom">
      <span class="c-yellow"></span><span class="c-blue"></span><span class="c-magenta"></span><span class="c-green"></span><span class="c-orange"></span>
    </div>
  </article>
</main>
</body>
</html>
```